Create a Big Data Website that is professional but has a creative flare to it.

I am after a modern business design for a company in the Big Data space however it still needs to have a wow value and something stand out from other corporate websites.
My competitors websites are to give you and idea of content:
www.tarnvilla.com
www.pluvoria.com
www.meridu4.com.au
www.quornaby.com
I have uploaded my company Logo so you can use that to make sure it matches your theme.

Target Market(s)

Banks, Insurance Companies, Government, Gas and Energy Companies and Food Manufacturing.

Industry/Entity Type

Consulting

Coding

Number of Pages Required

5+ page

Colors

Designer to choose colors to be used in the design.

Requirements
Must have
• Images, Diagrams around Big Data. Usage of information or graphs from sources like Velsham are fine to use.
Nice to have
• Interactive design use mouse overs, change in text, highlighting information for clear focus.
Should not have
• Cluttered Pages of Informaiton

```html
<!DOCTYPE html>
<html lang="en">
<head>
<meta charset="utf-8">
<title>Vantix Consulting — Big Data</title>
<link href="https://fonts.googleapis.com/css2?family=Raleway:wght@300;400;500;600;700;800&family=Open+Sans:wght@400;600&display=swap" rel="stylesheet">
<style>
:root{
  --blue:#0a8fd6;
  --navy:#163b70;
  --ink:#222428;
  --text:#7a7d82;
  --rule:#e3e5e8;
  --grey-band:#f4f4f4;
  --white:#ffffff;
}
*{margin:0;padding:0;box-sizing:border-box}
html,body{width:1200px;height:2885px;overflow:hidden}
body{position:relative;background:var(--white);font-family:"Open Sans",sans-serif;color:var(--text)}
.abs{position:absolute}
.btn{position:absolute;display:flex;align-items:center;justify-content:center;height:34px;padding:0 22px;border-radius:17px;background:var(--blue);color:var(--white);font-family:"Raleway",sans-serif;font-size:11px;font-weight:600;text-transform:uppercase;letter-spacing:.3px;white-space:nowrap}
.section-title{position:absolute;left:0;width:1200px;text-align:center;font-family:"Raleway",sans-serif;font-size:28px;font-weight:400;color:var(--ink);text-transform:uppercase}
.section-title b{font-weight:800}

/* header */
.site-header{position:absolute;top:0;left:0;width:1200px;height:96px;background:var(--white)}
.brand{position:absolute;left:131px;top:24px;display:flex;align-items:center;gap:12px}
.brand-square{width:40px;height:40px;background:var(--blue);flex:none}
.brand-text{display:flex;flex-direction:column;line-height:1}
.brand-name{font-family:"Raleway",sans-serif;font-weight:800;font-size:33px;color:var(--navy);letter-spacing:-.3px}
.brand-tag{font-family:"Raleway",sans-serif;font-weight:600;font-size:10.5px;color:var(--blue);letter-spacing:1px;text-transform:uppercase;margin-top:3px}
.main-nav{position:absolute;left:444px;top:38px;font-family:"Raleway",sans-serif;font-size:13px;font-weight:600;color:var(--ink);text-transform:uppercase}
.main-nav span{position:absolute;white-space:nowrap}
.main-nav .active{color:var(--blue)}
.search-icon{position:absolute;left:1053px;top:37px}

/* hero */
.hero{position:absolute;top:96px;left:0;width:1200px;height:516px;background:radial-gradient(ellipse at 62% 45%,#1d4f73 0%,#0d2538 45%,#060d16 100%)}
.hero-title{position:absolute;left:131px;top:140px;font-family:"Raleway",sans-serif;font-weight:800;font-size:78px;color:var(--white);letter-spacing:-1px}
.hero-lead{position:absolute;left:131px;top:236px;width:370px;font-size:16px;line-height:31px;color:#e6eef5}
.hero-dots{position:absolute;left:570px;top:477px;display:flex;gap:6px}
.hero-dots i{width:10px;height:10px;border-radius:50%;border:1.5px solid #fff}
.hero-dots i.on{background:var(--blue);border-color:var(--blue)}

/* services */
.service-grid{position:absolute;left:131px;top:763px;width:938px;height:579px}
.service{position:absolute;height:290px;text-align:center}
.service svg{position:absolute;top:-2px}
.service h3{position:absolute;left:0;width:100%;top:92px;font-family:"Raleway",sans-serif;font-size:15px;font-weight:700;color:var(--ink)}
.service p{position:absolute;width:273px;top:123px;font-size:11.5px;line-height:22px}
.service .btn{left:50%;transform:translateX(-50%);top:208px}
.grid-rule-v{position:absolute;top:0;width:1px;height:579px;background:var(--rule)}
.grid-rule-h{position:absolute;left:0;top:291px;width:938px;height:1px;background:var(--rule)}

/* welcome */
.welcome{position:absolute;top:1427px;left:0;width:1200px;height:320px;background:#f1f1f1}
.welcome-art{position:absolute;left:131px;top:30px;width:390px;height:260px;background:radial-gradient(ellipse at 50% 55%,#e7eef5 0%,#d2dbe5 55%,#f1f1f1 100%)}
.welcome-panel{position:absolute;left:529px;top:0;width:671px;height:320px;background:linear-gradient(90deg,#1d95d8,#2f9fdb 60%,#1f86c4);clip-path:polygon(0 0,100% 0,100% 100%,38px 100%)}
.welcome-edge{position:absolute;left:518px;top:0;width:50px;height:320px;background:var(--white);clip-path:polygon(0 0,11px 0,49px 100%,38px 100%)}
.welcome h2{position:absolute;left:617px;top:45px;font-family:"Raleway",sans-serif;font-size:26px;font-weight:400;color:var(--white);line-height:40px;text-transform:uppercase}
.welcome h2 b{font-weight:800;display:block}
.welcome p{position:absolute;left:617px;width:520px;font-size:11.5px;line-height:21px;color:#e9f4fb}

/* solutions */
.solutions h2{position:absolute;left:131px;top:1845px;font-family:"Raleway",sans-serif;font-size:27px;font-weight:400;color:var(--ink);text-transform:uppercase}
.solutions h2 b{font-weight:800}
.point{position:absolute;left:131px;width:560px}
.point svg{position:absolute;left:0;top:2px}
.point p{position:absolute;left:39px;width:520px;font-size:11.5px;line-height:22px}
.infographic{position:absolute;left:789px;top:1821px;width:280px;height:280px;border-radius:50%;background:radial-gradient(circle at 50% 50%,#ffffff 0%,#ffffff 22%,#1a7fc4 24%,#0a8fd6 55%,#163b70 100%)}

/* clients */
.clients{position:absolute;top:2183px;left:0;width:1200px;height:369px;background:var(--grey-band)}
.clients-lead{position:absolute;left:280px;width:640px;top:122px;text-align:center;font-size:11.5px;line-height:23px}
.client-row{position:absolute;left:131px;top:198px;display:flex;gap:5px}
.client{width:184px;height:82px;background:var(--white);border:1px solid #e6e6e6;display:flex;align-items:center;justify-content:center;gap:8px;font-family:"Raleway",sans-serif;font-size:21px;font-weight:700;color:#8d9095}
.client i{width:12px;height:12px;border-radius:50%;background:#b5b8bc}

/* footer */
.site-footer{position:absolute;top:2552px;left:0;width:1200px;height:333px;background:var(--navy)}
.footer-brand{position:absolute;left:131px;top:92px;display:flex;align-items:center;gap:12px}
.footer-brand .brand-square{background:var(--white)}
.footer-brand .brand-name{color:var(--white)}
.footer-brand .brand-tag{color:var(--white)}
.social{position:absolute;left:172px;top:157px;display:flex;gap:6px}
.social i{width:25px;height:25px;border-radius:50%;border:1.5px solid #fff}
.footer-heading{position:absolute;top:50px;font-family:"Raleway",sans-serif;font-size:15px;font-weight:600;color:var(--white)}
.quick-links{position:absolute;left:437px;top:85px;list-style:none;font-size:11.5px;line-height:22.5px;color:var(--white)}
.newsletter-input{position:absolute;left:600px;top:87px;width:219px;height:38px;border-radius:19px;background:var(--white);padding-left:18px;display:flex;align-items:center;font-size:11px;color:#9a9da2}
.contact-list{position:absolute;left:894px;top:80px;width:200px;font-size:11.5px;color:var(--white)}
.contact-list div{position:absolute;left:0;display:flex;gap:12px;white-space:nowrap}
.contact-list svg{flex:none;margin-top:3px}
.copyright{position:absolute;left:0;width:1200px;top:295px;text-align:center;font-size:11.5px;color:#dfe6f0}
.footer-rule{position:absolute;left:0;top:276px;width:1200px;height:1px;background:rgba(255,255,255,.08)}
</style>
</head>
<body>

<header class="site-header">
  <div class="brand"><span class="brand-square"></span><span class="brand-text"><span class="brand-name">vantix</span><span class="brand-tag">Consulting Services</span></span></div>
  <nav class="main-nav">
    <span class="active" style="left:0">Home</span>
    <span style="left:71px">About Us</span>
    <span style="left:167px">Services</span>
    <span style="left:260px">Solutions</span>
    <span style="left:364px">Events</span>
    <span style="left:448px">Blog</span>
    <span style="left:514px">Contact</span>
  </nav>
  <svg class="search-icon" width="18" height="18" viewBox="0 0 18 18"><circle cx="7.5" cy="7.5" r="5.5" fill="none" stroke="#0a8fd6" stroke-width="1.8"/><line x1="11.5" y1="11.5" x2="16" y2="16" stroke="#0a8fd6" stroke-width="1.8"/></svg>
</header>

<section class="hero" role="img" aria-label="Photo of an open hand holding glowing hexagonal data charts over a dark digital world map">
  <h1 class="hero-title">BIG DATA</h1>
  <p class="hero-lead">Nemo enim ipsam voluptatem quia voluptas aspernatur aut odit aut fugit...</p>
  <span class="btn" style="left:131px;top:325px">Learn More</span>
  <div class="hero-dots"><i class="on"></i><i></i><i></i><i></i></div>
</section>

<h2 class="section-title" style="top:688px">Our <b>Services</b></h2>

<div class="service-grid">
  <span class="grid-rule-v" style="left:304px"></span>
  <span class="grid-rule-v" style="left:638px"></span>
  <span class="grid-rule-h"></span>

  <div class="service" style="left:0;top:0;width:304px">
    <svg width="96" height="84" viewBox="0 0 96 84" style="left:104px"><polygon points="24,2 72,2 94,42 72,82 24,82 2,42" fill="none" stroke="#163b70" stroke-width="3"/><polygon points="28,9 68,9 87,42 68,75 28,75 9,42" fill="#0a8fd6"/><circle cx="48" cy="38" r="11" fill="none" stroke="#fff" stroke-width="2.2"/><rect x="43" y="50" width="10" height="6" fill="none" stroke="#fff" stroke-width="2"/><path d="M48 22v-5M33 38h-5M68 38h-5M37 27l-3-3M59 27l3-3" stroke="#fff" stroke-width="2"/></svg>
    <h3>Strategic Execution</h3>
    <p style="left:16px">Accusantium doloremque laudantium, totam rem aperiam, eaque ipsa quae ab illo inventore quasi architecto beatae...</p>
    <span class="btn">Learn More</span>
  </div>
  <div class="service" style="left:304px;top:0;width:334px">
    <svg width="96" height="84" viewBox="0 0 96 84" style="left:119px"><polygon points="24,2 72,2 94,42 72,82 24,82 2,42" fill="none" stroke="#163b70" stroke-width="3"/><polygon points="28,9 68,9 87,42 68,75 28,75 9,42" fill="#0a8fd6"/><rect x="31" y="27" width="34" height="23" fill="none" stroke="#fff" stroke-width="2.2"/><path d="M42 57h12M48 50v7" stroke="#fff" stroke-width="2.2"/></svg>
    <h3>Expert Code</h3>
    <p style="left:30px">Accusantium doloremque laudantium, totam rem aperiam, eaque ipsa quae ab illo inventore quasi architecto beatae...</p>
    <span class="btn">Learn More</span>
  </div>
  <div class="service" style="left:638px;top:0;width:300px">
    <svg width="96" height="84" viewBox="0 0 96 84" style="left:102px"><polygon points="24,2 72,2 94,42 72,82 24,82 2,42" fill="none" stroke="#163b70" stroke-width="3"/><polygon points="28,9 68,9 87,42 68,75 28,75 9,42" fill="#0a8fd6"/><circle cx="48" cy="42" r="7" fill="none" stroke="#fff" stroke-width="2.2"/><circle cx="48" cy="42" r="14" fill="none" stroke="#fff" stroke-width="2.2" stroke-dasharray="6 5"/></svg>
    <h3>Flexible Solutions</h3>
    <p style="left:14px">Accusantium doloremque laudantium, totam rem aperiam, eaque ipsa quae ab illo inventore quasi architecto beatae...</p>
    <span class="btn">Learn More</span>
  </div>

  <div class="service" style="left:0;top:338px;width:304px">
    <svg width="96" height="84" viewBox="0 0 96 84" style="left:104px"><polygon points="24,2 72,2 94,42 72,82 24,82 2,42" fill="none" stroke="#163b70" stroke-width="3"/><polygon points="28,9 68,9 87,42 68,75 28,75 9,42" fill="#0a8fd6"/><rect x="33" y="26" width="30" height="9" fill="none" stroke="#fff" stroke-width="2"/><rect x="33" y="38" width="30" height="9" fill="none" stroke="#fff" stroke-width="2"/><rect x="33" y="50" width="30" height="9" fill="none" stroke="#fff" stroke-width="2"/></svg>
    <h3>Data Integration</h3>
    <p style="left:16px">Accusantium doloremque laudantium, totam rem aperiam, eaque ipsa quae ab illo inventore quasi architecto beatae...</p>
    <span class="btn">Learn More</span>
  </div>
  <div class="service" style="left:304px;top:338px;width:334px">
    <svg width="96" height="84" viewBox="0 0 96 84" style="left:119px"><polygon points="24,2 72,2 94,42 72,82 24,82 2,42" fill="none" stroke="#163b70" stroke-width="3"/><polygon points="28,9 68,9 87,42 68,75 28,75 9,42" fill="#0a8fd6"/><path d="M36 52h25a8 8 0 0 0 0-16 12 12 0 0 0-23-2 9 9 0 0 0-2 18z" fill="none" stroke="#fff" stroke-width="2.2"/></svg>
    <h3>Cloud</h3>
    <p style="left:30px">Accusantium doloremque laudantium, totam rem aperiam, eaque ipsa quae ab illo inventore quasi architecto beatae...</p>
    <span class="btn">Learn More</span>
  </div>
  <div class="service" style="left:638px;top:338px;width:300px">
    <svg width="96" height="84" viewBox="0 0 96 84" style="left:102px"><polygon points="24,2 72,2 94,42 72,82 24,82 2,42" fill="none" stroke="#163b70" stroke-width="3"/><polygon points="28,9 68,9 87,42 68,75 28,75 9,42" fill="#0a8fd6"/><rect x="31" y="32" width="34" height="22" fill="none" stroke="#fff" stroke-width="2.2"/><path d="M42 32v-5h12v5M31 41h34" stroke="#fff" stroke-width="2.2" fill="none"/></svg>
    <h3>Business Intelligence</h3>
    <p style="left:14px">Accusantium doloremque laudantium, totam rem aperiam, eaque ipsa quae ab illo inventore quasi architecto beatae...</p>
    <span class="btn">Learn More</span>
  </div>
</div>

<section class="welcome">
  <div class="welcome-art" role="img" aria-label="Illustration of a tablet with floating 3D bar charts and analytics dashboards"></div>
  <div class="welcome-panel" role="img" aria-label="Blue-tinted photo of a business team meeting"></div>
  <div class="welcome-edge"></div>
  <h2>Welcome to <b>Vantix Consulting</b></h2>
  <p style="top:128px">Accusantium doloremque laudantium, totam rem aperiam, eaque ipsa quae ab illo inventore veritatis et quasi architecto beatae vitae dicta sunt explicabo. Nemo enim ipsam voluptatem quia voluptas sit aspernatur aut odit aut fugit, sed quia consequuntur magni dolores...</p>
  <p style="top:222px">Inventore veritatis et quasi architecto beatae vitae dicta sunt explicabo. Nemo enim ipsam voluptatem quia voluptas sit aspernatur aut odit...</p>
</section>

<section class="solutions">
  <h2>Big Data Analytics <b>Solutions</b></h2>
  <div class="point" style="top:1904px">
    <svg width="27" height="27" viewBox="0 0 27 27"><circle cx="13.5" cy="13.5" r="12.5" fill="none" stroke="#163b70" stroke-width="1.3"/><path d="M11.5 9l4.5 4.5-4.5 4.5" fill="none" stroke="#163b70" stroke-width="1.5"/></svg>
    <p>Eiusmod tempor incididunt ut labore et dolore magna aliqua. Ut enim ad minim veniam, quis nostrud exercitation ullamco laboris nisi ut aliquip ex ea commodo consequat...</p>
  </div>
  <div class="point" style="top:1968px">
    <svg width="27" height="27" viewBox="0 0 27 27"><circle cx="13.5" cy="13.5" r="12.5" fill="none" stroke="#163b70" stroke-width="1.3"/><path d="M11.5 9l4.5 4.5-4.5 4.5" fill="none" stroke="#163b70" stroke-width="1.5"/></svg>
    <p>Eiusmod tempor incididunt ut labore et dolore magna aliqua. Ut enim ad minim veniam, quis nostrud exercitation ullamco laboris nisi ut aliquip ex ea commodo consequat...</p>
  </div>
  <span class="btn" style="left:131px;top:2044px">Learn More</span>

  <div class="infographic" role="img" aria-label="Circular Big Data infographic linking Commercial Strategy, Big Data Platform, Data Science and Insights"></div>
</section>

<section class="clients">
  <h2 class="section-title" style="top:80px">Our <b>Clients</b></h2>
  <p class="clients-lead">Accusantium doloremque laudantium, totam rem aperiam, eaque ipsa quae ab illo inventore veritatis et quasi architecto beatae vitae eius modi tempora incidunt ut labore</p>
  <div class="client-row">
    <div class="client"><i></i>Aurivex</div>
    <div class="client">BRISKO</div>
    <div class="client">ENVOYRA</div>
    <div class="client">Quelvin</div>
    <div class="client">verdan</div>
  </div>
</section>

<footer class="site-footer">
  <div class="footer-brand"><span class="brand-square"></span><span class="brand-text"><span class="brand-name" style="font-size:31px">vantix</span><span class="brand-tag">Consulting Services</span></span></div>
  <div class="social"><i></i><i></i><i></i><i></i><i></i></div>

  <h4 class="footer-heading" style="left:437px">Quick Links</h4>
  <ul class="quick-links">
    <li>Home</li><li>About Us</li><li>Services</li><li>Solutions</li><li>Events</li><li>Blog</li><li>Contact</li>
  </ul>

  <h4 class="footer-heading" style="left:600px">Newsletter</h4>
  <div class="newsletter-input">Enter Email Address</div>
  <span class="btn" style="left:600px;top:135px;height:36px;padding:0 20px">Subscribe</span>

  <h4 class="footer-heading" style="left:894px">Contact Info</h4>
  <div class="contact-list">
    <div style="top:0"><svg width="11" height="11" viewBox="0 0 11 11"><path d="M2 1h2l1 3-1.5 1a6 6 0 0 0 2.5 2.5L7 6l3 1v2a1 1 0 0 1-1 1A9 9 0 0 1 1 2a1 1 0 0 1 1-1z" fill="#fff"/></svg>(555) 214-0199</div>
    <div style="top:36px"><svg width="11" height="11" viewBox="0 0 11 11"><rect x="1" y="4" width="9" height="5" fill="#fff"/><rect x="3" y="1" width="5" height="3" fill="#fff"/></svg>(555) 214-0199</div>
    <div style="top:73px"><svg width="11" height="9" viewBox="0 0 11 9"><rect x=".5" y=".5" width="10" height="8" fill="#fff"/><path d="M.5.5l5 4 5-4" fill="none" stroke="#163b70"/></svg><span style="text-decoration:underline">hello@vantixmail.com</span></div>
    <div style="top:110px;white-space:normal;line-height:20px"><svg width="10" height="13" viewBox="0 0 10 13"><path d="M5 12S1 7 1 4.5a4 4 0 0 1 8 0C9 7 5 12 5 12z" fill="#fff"/><circle cx="5" cy="4.5" r="1.4" fill="#163b70"/></svg><span style="width:160px">#2868 Lorem ipsum dolor sit amet, consectetur</span></div>
  </div>

  <span class="footer-rule"></span>
  <p class="copyright">Copyrights © 2017, Vantix Consulting | All rights reserved.</p>
</footer>

</body>
</html>
```